Web Design Project for a beach town business owner who supports new families with their babies.

I'm looking for a basic website with the following pages: home, about, services, FAQs, blog, and contact page. I have images and content ready to go.

Target Market(s)

Men and women between the ages of 22 and 42, growing families

Industry/Entity Type

Postpartum Doula

Coding

Number of Pages Required

Font styles to use
Serif
Other font styles liked:
• My logo font is "Nexa Bold" - so coordinating fonts with that are ideal

Colors
00AB8E
00BBA5
67D7C9
C6EFE9
E9F9F6
EE7325
F08F49
F5BC92
FAE3D3
FDF4ED

Requirements
Must have
• Warm and professional vibe, multicultural images, aligned with my branding colors and font ("Nexa Bold"; COLORS: light blue hex: #2FCEC2 R: 47 G: 206 B: 194 dark blue hex: #007C7C R: 0 G: 124 B: 124 orange hex: #F77B4E R: 247 G: 123 B: 78), good SEO
Should not have
• Ultra feminine images, baby bottles, cutesy images.

```html
<!DOCTYPE html>
<html lang="en">
<head>
<meta charset="utf-8">
<title>Harborlight Families Postpartum Care</title>
<link href="https://fonts.googleapis.com/css2?family=Urbanist:wght@400;500;600;700;800;900&display=swap" rel="stylesheet">
<style>
:root{
  --teal:#2FC4B2;
  --teal-deep:#1FA383;
  --orange:#E8601E;
  --field:#5B1F0A;
  --mint:#E6F6F3;
  --ink:#2A2A2A;
  --muted:#555;
  --white:#fff;
}
*{box-sizing:border-box;margin:0;padding:0}
html,body{width:1200px;height:3184px;overflow:hidden}
body{position:relative;font-family:"Urbanist",sans-serif;color:var(--ink);background:var(--white)}
.abs{position:absolute}
.btn{position:absolute;background:var(--teal);color:var(--white);font-weight:700;letter-spacing:2px;font-size:16px;display:flex;align-items:center;justify-content:center;text-transform:uppercase}

/* hero */
.hero{left:0;top:0;width:1200px;height:868px;background:linear-gradient(135deg,#5a524c 0%,#3c3632 45%,#2a2624 100%)}
.hero-shade{left:0;top:0;width:1200px;height:868px;background:linear-gradient(90deg,rgba(0,0,0,.15),rgba(0,0,0,.35))}
.nav{left:111px;top:54px;width:977px;height:62px;background:var(--white)}
.nav-logo{left:125px;top:23px;width:124px;height:124px;border-radius:50%;background:var(--white);display:flex;align-items:center;justify-content:center;text-align:center}
.nav-logo span{border:3px solid var(--teal);border-radius:50%;height:96px;width:96px;display:flex;align-items:center;justify-content:center;font-size:12px;font-weight:700;color:var(--teal);line-height:1.25}
.nav-links{right:322px;top:73px;display:flex;gap:24px;font-size:16px;font-weight:600;color:#444}
.welcome{left:111px;top:503px;color:var(--white);font-size:20px;font-weight:700;letter-spacing:8px}
.hero-title{left:111px;top:528px;color:var(--white);font-size:44px;font-weight:800;letter-spacing:-.5px;white-space:nowrap}
.hero-sub{left:111px;top:588px;color:var(--white);font-size:37px;font-weight:800;letter-spacing:-.5px}
.hero-text{left:111px;top:636px;width:490px;color:var(--white);font-size:13.5px;font-weight:700;line-height:27px}

.form{left:659px;top:116px;width:429px;height:752px;background:var(--orange)}
.form h2{position:absolute;left:0;width:429px;top:42px;text-align:center;color:var(--white);font-size:28px;font-weight:800}
.field{position:absolute;left:49px;width:331px;background:var(--field);color:var(--white);font-size:11.5px;font-weight:700;padding:0 17px;display:flex;align-items:center}
.field.tall{display:block;padding-top:14px}
.field .caret{position:absolute;right:14px;top:50%;margin-top:-3px;border:5px solid transparent;border-top-color:#fff;border-bottom:0}
.field .cal{position:absolute;right:12px;top:50%;margin-top:-6px;width:11px;height:11px;border:2px solid #fff}
.checks{display:flex;gap:18px;margin-top:13px}
.checks i{display:inline-block;width:9px;height:9px;border:1px solid #fff;margin-right:8px;vertical-align:-1px}

/* services */
.sec-title{color:var(--teal);font-size:44px;font-weight:800}
.services-photo{left:103px;top:1032px;width:322px;height:400px;border-radius:50%;background:linear-gradient(160deg,#7a5a4c,#3a2a30 55%,#d8a4b4);box-shadow:-6px 0 0 var(--orange)}
.services-lead{left:467px;top:1016px;width:640px;font-size:17.5px;font-weight:700;line-height:27.4px;color:#333}
.services-list{left:467px;top:1169px;list-style:none;font-size:16px;font-weight:500;color:#555;line-height:27.4px}
.services-list li{display:flex;align-items:center;gap:14px}
.services-list svg{flex:none}
.rule-orange{left:0;top:1627px;width:1200px;height:5px;background:var(--orange)}

/* about */
.about{left:0;top:1632px;width:1200px;height:625px;background:var(--mint)}
.rule-teal{left:0;top:2257px;width:1200px;height:5px;background:var(--teal)}
.about-text{left:111px;top:1795px;width:505px;font-size:13.5px;font-weight:600;line-height:24px;color:#3a3a3a}
.about-photo{left:687px;top:1743px;width:400px;height:400px;border-radius:50%;border:4px solid var(--teal);background:radial-gradient(circle at 50% 40%,#c89a82,#6f7a52 55%,#3f5a3a)}

/* faq */
.faq-title{left:0;width:1200px;top:2372px;text-align:center}
.faq-item{position:absolute;left:220px;width:760px;height:73px;border:1px solid #bbb;display:flex;align-items:center;padding-left:37px;font-size:17.5px;font-weight:700;color:#222}
.faq-item svg{position:absolute;right:36px;top:27px}

/* footer */
.footer{left:0;top:2937px;width:1200px;height:247px;background:var(--teal-deep)}
.foot-logo{left:109px;top:2967px;width:120px;height:120px;border-radius:50%;background:var(--white);display:flex;align-items:center;justify-content:center;text-align:center;font-size:14px;font-weight:700;color:var(--teal);line-height:1.3}
.social{left:266px;top:3018px;display:flex;gap:13px}
.social i{display:block;width:22px;height:22px;border-radius:50%;background:var(--white)}
.vline{top:2979px;width:1px;height:107px;background:rgba(255,255,255,.45)}
.foot-text{font-size:17px;font-weight:700;line-height:28px;color:var(--white)}
.hline{left:111px;top:3104px;width:977px;height:1px;background:rgba(255,255,255,.25)}
.copy{left:111px;top:3131px;font-size:11.5px;font-weight:700;color:var(--white)}
.foot-links{right:112px;top:3131px;display:flex;gap:20px;font-size:11.5px;font-weight:700;color:var(--white)}
</style>
</head>
<body>

<div class="abs hero" role="img" aria-label="Photo of a postpartum doula sitting with a new mother holding her newborn"></div>
<div class="abs hero-shade"></div>

<div class="abs nav"></div>
<div class="abs nav-logo"><span>Harborlight Families</span></div>
<nav class="abs nav-links"><span>Home</span><span>About</span><span>Services</span><span>FAQs</span><span>Blog</span><span>Contact</span></nav>
<div class="btn" style="left:903px;top:64px;width:175px;height:42px">Get Started</div>

<div class="abs welcome">WELCOME TO</div>
<h1 class="abs hero-title">HARBORLIGHT FAMILIES</h1>
<div class="abs hero-sub">POSTPARTUM CARE!</div>
<p class="abs hero-text">Hi, I'm Dana Reyes, a certified postpartum care expert and educator serving families of all varieties in the greater San Diego area and beyond.</p>
<div class="btn" style="left:111px;top:707px;width:235px;height:42px">Let's Get Started</div>

<form class="abs form">
  <h2>LET'S GET STARTED</h2>
  <div class="field" style="top:82px;height:38px">Name*</div>
  <div class="field" style="top:125px;height:38px">Email*</div>
  <div class="field" style="top:167px;height:38px">Phone #*</div>
  <div class="field tall" style="top:210px;height:74px">Have you had your baby(ies), yet?*
    <div class="checks"><span><i></i>Yes</span><span><i></i>No</span></div></div>
  <div class="field" style="top:289px;height:39px;font-size:10px">If so, did you have a birth canal or a surgical birth?<b class="caret"></b></div>
  <div class="field" style="top:333px;height:38px;font-size:10px">If not, what is your EDD?<b class="cal"></b></div>
  <div class="field tall" style="top:376px;height:74px">Is this your first baby?*
    <div class="checks"><span><i></i>Yes</span><span><i></i>No</span></div></div>
  <div class="field tall" style="top:455px;height:74px">If not, what are the ages of your older children?</div>
  <div class="field" style="top:534px;height:38px;font-size:10px">Are you interested in in-person or virtual support?*<b class="caret"></b></div>
  <div class="field tall" style="top:577px;height:76px">I'd just like to add:</div>
  <div class="btn" style="left:97px;top:660px;width:235px;height:42px">Let's Get Started</div>
</form>

<h2 class="abs sec-title" style="left:467px;top:948px">SERVICES</h2>
<div class="abs services-photo" role="img" aria-label="Portrait of the doula cradling a sleeping newborn"></div>
<div class="abs services-lead">
  What does a typical postpartum care shift look like?<br>
  I will come to you.<br>
  I will meet you where you are on your parenting journey.<br>
  You do not have to dry your tears, get out of your pajamas, brush your hair or teeth, take a shower, or clean your house before I arrive.
</div>
<ul class="abs services-list">
  <li><svg width="15" height="15" viewBox="0 0 16 16"><circle cx="8" cy="8" r="8" fill="#E8601E"/><path d="M4 8h7M8 4.5 11.5 8 8 11.5" stroke="#fff" stroke-width="2" fill="none"/></svg>Wash and fold laundry</li>
  <li><svg width="15" height="15" viewBox="0 0 16 16"><circle cx="8" cy="8" r="8" fill="#E8601E"/><path d="M4 8h7M8 4.5 11.5 8 8 11.5" stroke="#fff" stroke-width="2" fill="none"/></svg>Tidy up common living space</li>
  <li><svg width="15" height="15" viewBox="0 0 16 16"><circle cx="8" cy="8" r="8" fill="#E8601E"/><path d="M4 8h7M8 4.5 11.5 8 8 11.5" stroke="#fff" stroke-width="2" fill="none"/></svg>Load/unload dishwasher</li>
  <li><svg width="15" height="15" viewBox="0 0 16 16"><circle cx="8" cy="8" r="8" fill="#E8601E"/><path d="M4 8h7M8 4.5 11.5 8 8 11.5" stroke="#fff" stroke-width="2" fill="none"/></svg>Take trash out</li>
  <li><svg width="15" height="15" viewBox="0 0 16 16"><circle cx="8" cy="8" r="8" fill="#E8601E"/><path d="M4 8h7M8 4.5 11.5 8 8 11.5" stroke="#fff" stroke-width="2" fill="none"/></svg>Organize baby supplies/nursery</li>
  <li><svg width="15" height="15" viewBox="0 0 16 16"><circle cx="8" cy="8" r="8" fill="#E8601E"/><path d="M4 8h7M8 4.5 11.5 8 8 11.5" stroke="#fff" stroke-width="2" fill="none"/></svg>Sanitize baby bottles</li>
  <li><svg width="15" height="15" viewBox="0 0 16 16"><circle cx="8" cy="8" r="8" fill="#E8601E"/><path d="M4 8h7M8 4.5 11.5 8 8 11.5" stroke="#fff" stroke-width="2" fill="none"/></svg>Wash pump parts</li>
  <li><svg width="15" height="15" viewBox="0 0 16 16"><circle cx="8" cy="8" r="8" fill="#E8601E"/><path d="M4 8h7M8 4.5 11.5 8 8 11.5" stroke="#fff" stroke-width="2" fill="none"/></svg>Light meal prep (chopping veggies, filling a crockpot, etc.)</li>
  <li><svg width="15" height="15" viewBox="0 0 16 16"><circle cx="8" cy="8" r="8" fill="#E8601E"/><path d="M4 8h7M8 4.5 11.5 8 8 11.5" stroke="#fff" stroke-width="2" fill="none"/></svg>Make art, reading to or play with older kiddo(s)</li>
  <li><svg width="15" height="15" viewBox="0 0 16 16"><circle cx="8" cy="8" r="8" fill="#E8601E"/><path d="M4 8h7M8 4.5 11.5 8 8 11.5" stroke="#fff" stroke-width="2" fill="none"/></svg>Love on your pet(s)</li>
  <li><svg width="15" height="15" viewBox="0 0 16 16"><circle cx="8" cy="8" r="8" fill="#E8601E"/><path d="M4 8h7M8 4.5 11.5 8 8 11.5" stroke="#fff" stroke-width="2" fill="none"/></svg>Run a quick errand (dry-cleaning, post office drop-off, light grocery shopping, etc.)</li>
</ul>
<div class="btn" style="left:467px;top:1496px;width:235px;height:42px">Let's Get Started</div>
<div class="abs rule-orange"></div>

<section class="abs about"></section>
<h2 class="abs sec-title" style="left:111px;top:1727px">ABOUT ME</h2>
<div class="abs about-text">
  <p>Dana (she/her/hers) is a former Keystone certified birth advocate and support provider (also known as a doula) and childbirth educator who has supported over 200 growing families between the years 2015 and 2021. She received her Bachelor of Arts in Liberal Studies with an emphasis on Spanish and a lifetime teaching credential from Bayview State University in the year 2000 – providing her with a deep understanding of child growth and development and educational theory and techniques.</p>
  <p style="margin-top:24px">&nbsp;She had a blast teaching first through fourth grade students from 2000-2012 in the San Francisco Bay Area. She currently lives on the traditional, ancestral, and unceded land of the Kumeyaay Nation and its peoples, also known as San Diego County, with her wife, daughter, and four fur babies.</p>
</div>
<div class="btn" style="left:111px;top:2105px;width:234px;height:42px">Read More About</div>
<div class="abs about-photo" role="img" aria-label="Smiling headshot portrait of the doula outdoors"></div>
<div class="abs rule-teal"></div>

<h2 class="abs sec-title faq-title">FAQ</h2>
<div class="faq-item" style="top:2451px">What is a postpartum care expert (doula)?<svg width="17" height="17" viewBox="0 0 16 16"><circle cx="8" cy="8" r="8" fill="#2FC4B2"/><path d="M8 4v8M4 8h8" stroke="#fff" stroke-width="2"/></svg></div>
<div class="faq-item" style="top:2537px">Do you provide nanny services?<svg width="17" height="17" viewBox="0 0 16 16"><circle cx="8" cy="8" r="8" fill="#2FC4B2"/><path d="M8 4v8M4 8h8" stroke="#fff" stroke-width="2"/></svg></div>
<div class="faq-item" style="top:2623px">What kinds of medical support can you offer?<svg width="17" height="17" viewBox="0 0 16 16"><circle cx="8" cy="8" r="8" fill="#2FC4B2"/><path d="M8 4v8M4 8h8" stroke="#fff" stroke-width="2"/></svg></div>
<div class="faq-item" style="top:2717px">Are you available for overnight shifts?<svg width="17" height="17" viewBox="0 0 16 16"><circle cx="8" cy="8" r="8" fill="#2FC4B2"/><path d="M8 4v8M4 8h8" stroke="#fff" stroke-width="2"/></svg></div>

<footer class="abs footer"></footer>
<div class="abs foot-logo">Harborlight<br>Families</div>
<div class="abs social"><i></i><i></i><i></i><i></i></div>
<div class="abs vline" style="left:477px"></div>
<div class="abs vline" style="left:817px"></div>
<svg class="abs" style="left:533px;top:2977px" width="14" height="20" viewBox="0 0 14 20"><path d="M7 0C3 0 0 3 0 7c0 5 7 13 7 13s7-8 7-13c0-4-3-7-7-7z" fill="#fff"/><circle cx="7" cy="7" r="2.6" fill="#1FA383"/></svg>
<div class="abs foot-text" style="left:581px;top:2973px">412 Marlow Lane,<br>Oakridge,<br>Illinois, 60412.</div>
<svg class="abs" style="left:876px;top:2978px" width="18" height="18" viewBox="0 0 24 24"><path d="M6.6 10.8c1.4 2.8 3.8 5.1 6.6 6.6l2.2-2.2c.3-.3.7-.4 1-.2 1.1.4 2.3.6 3.6.6.6 0 1 .4 1 1V20c0 .6-.4 1-1 1C10.6 21 3 13.4 3 4c0-.6.4-1 1-1h3.5c.6 0 1 .4 1 1 0 1.3.2 2.5.6 3.6.1.3 0 .7-.2 1z" fill="#fff"/></svg>
<div class="abs foot-text" style="left:923px;top:2973px">+ 555-214-0198</div>
<svg class="abs" style="left:876px;top:3039px" width="18" height="18" viewBox="0 0 18 18"><path d="M1 7 9 1l8 6v10H1z" fill="#fff"/><path d="M1 7l8 6 8-6" stroke="#1FA383" stroke-width="1.5" fill="none"/></svg>
<div class="abs foot-text" style="left:923px;top:3034px">hello@harborlight.com</div>
<div class="abs hline"></div>
<div class="abs copy">© 2021 Harborlight Families.</div>
<div class="abs foot-links"><span>Home</span><span>About</span><span>Services</span><span>FAQs</span><span>Blog</span><span>Contact</span></div>

</body>
</html>
```